Brookvane Consulting Business Card Design

Business Card Design for Brookvane Consulting. Brookvane Consulting is a boutique consultancy based in Atlanta, GA., that specializes in marketing strategy, organization planning, and leadership development. We provide solutions for small businesses and startups as well as Vantage 300 companies.

http://brookvaneconsulting.com/

Target Market(s)

We provide solutions for small businesses and startups as well as Vantage 300 companies.

Industry/Entity Type

Consulting

Contact Information for Business Card

Two sided business card with priority on contact information, logo, tag line (Inspiration to Dream More, Do More, Become More)

Colors

Designer to choose colors to be used in the design.

Requirements
Must have
• contact information, logo, tag line (Inspiration to Dream More, Do More, Become More)
• Simple no over communication.
Nice to have
• I would like to see different placements of logo and creative use of both sides of the card
Should not have
• Do not put too much information on the card.

```html
<!DOCTYPE html>
<html lang="en">
<head>
<meta charset="utf-8">
<title>Brookvane Consulting – Business Card</title>
<link href="https://fonts.googleapis.com/css2?family=Roboto:wght@400;500;700&display=swap" rel="stylesheet">
<style>
  :root {
    --page-bg: #222224;
    --card-bg: #3a3a3c;
    --band-bg: #0c0c0d;
    --text-light: #f2f2f2;
    --text-muted: #9a9a9c;
    --logo-front: #bdbdbf;
  }
  * { margin: 0; padding: 0; box-sizing: border-box; }
  html, body {
    width: 799px; height: 1200px; overflow: hidden;
    background: var(--page-bg);
    font-family: "Roboto", sans-serif;
  }
  .canvas {
    position: relative; width: 799px; height: 1200px;
  }
  .card {
    position: absolute; left: 100px;
    width: 600px; height: 343px;
    background: var(--card-bg);
    border-radius: 30px;
    overflow: hidden;
    box-shadow: 0 14px 30px rgba(0,0,0,0.45);
  }
  .card--front { top: 110px; }
  .card--back { top: 720px; }

  .wordmark {
    font-weight: 500;
    line-height: 1.05;
    letter-spacing: 0.5px;
  }
  .card--front .wordmark {
    position: absolute; left: 0; right: 0; top: 118px;
    text-align: center;
    color: var(--logo-front);
    font-size: 46px;
  }
  .card--back .wordmark {
    position: absolute; left: 120px; top: 52px;
    color: var(--text-light);
    font-size: 38px;
  }

  .tagline-band {
    position: absolute; left: 0; top: 0; bottom: 0;
    width: 40px;
    background: var(--band-bg);
  }
  .tagline {
    position: absolute; left: 20px; top: 50%;
    transform: translate(-50%, -50%) rotate(-90deg);
    white-space: nowrap;
    color: var(--text-light);
    font-size: 12.5px;
    letter-spacing: 0.2px;
  }

  .contact {
    position: absolute; left: 120px; top: 186px;
    color: var(--text-light);
  }
  .contact__name {
    font-weight: 700; font-size: 22px;
    margin-bottom: 12px;
  }
  .contact__line {
    font-size: 15px; line-height: 1.4;
  }
</style>
</head>
<body>
<main class="canvas">
  <section class="card card--front" aria-label="Card front">
    <p class="wordmark">Brookvane Consulting</p>
  </section>

  <section class="card card--back" aria-label="Card back">
    <div class="tagline-band">
      <p class="tagline">Inspiration to Dream More, Do More, Become More</p>
    </div>
    <p class="wordmark">Brookvane Consulting</p>
    <div class="contact">
      <p class="contact__name">Dana</p>
      <p class="contact__line">555-014-2290</p>
      <p class="contact__line">dana@brookvaneconsulting.com</p>
      <p class="contact__line">www.brookvaneconsulting.com</p>
    </div>
  </section>
</main>
</body>
</html>
```